Web page design for a startup, no coding

Quorvix is a Data mining startup helping companies get data from websites. We’re looking to revamp our website to make it more professional and conversation friendly.
I need a designer to design the website in PSD and Once the PSD is done, the HTML design will be awarded as a separate job. We’ll need continues improvements to the design based on the user behaviour in the site and this can be a long term work for the right designer.
Read the details on the attached document
Target Market(s)
Big data, Data Mining
Industry/Entity Type
Business Software
Number of Pages Required
5+ page
Requirements
Must have
- Refer to the doc
Nice to have
- Refer to the doc
Should not have
- Refer to the doc

```html
<!DOCTYPE html>
<html lang="en">
<head>
<meta charset="utf-8">
<title>Quorvix — Structured Data Feeds</title>
<link href="https://fonts.googleapis.com/css2?family=Mulish:wght@400;600;700&display=swap" rel="stylesheet">
<style>
:root{
  --accent:#f7b016;
  --ink:#222222;
  --muted:#6f6f6f;
  --soft:#9a9a9a;
  --band:#f1f1f1;
  --hex-grey:#7b7b7b;
  --white:#ffffff;
  --line:#d9d9d9;
}
*{margin:0;padding:0;box-sizing:border-box}
html,body{width:1200px;height:2707px;overflow:hidden}
body{font-family:"Mulish",sans-serif;color:var(--ink);background:var(--white);position:relative}
.abs{position:absolute}

/* hero */
.hero{left:0;top:0;width:1200px;height:596px;clip-path:polygon(0 0,100% 0,100% 541px,50% 596px,0 541px);
  background:linear-gradient(100deg,#8d8e8c 0%,#b3b2ad 30%,#a9aaa6 55%,#c4c3bd 80%,#9fa39a 100%)}
.hero::after{content:"";position:absolute;inset:0;background:rgba(40,40,40,.35)}
.brand{font-weight:600;color:var(--white);font-size:34px;display:flex;align-items:center;gap:12px;z-index:2;white-space:nowrap}
.brand .mark{width:26px;height:26px;border:3px solid currentColor}
.nav{top:50px;left:599px;z-index:2}
.nav a{position:absolute;color:var(--white);font-weight:600;font-size:17px;text-decoration:none;white-space:nowrap}
.hero-title{top:225px;left:0;width:1200px;text-align:center;color:var(--white);font-size:37px;font-weight:600;z-index:2}
.hero-sub{top:280px;left:170px;width:860px;text-align:center;color:var(--white);font-size:20px;line-height:28px;z-index:2}
.btn{background:var(--accent);color:var(--white);font-weight:600;display:flex;align-items:center;justify-content:center;white-space:nowrap}
.hero-btn{left:519px;top:357px;width:122px;height:43px;font-size:16px;z-index:2}
.dots{top:561px;left:555px;display:flex;gap:8px}
.dots span{width:14px;height:14px;border-radius:50%;background:#9c9c9c;border:2px solid #9c9c9c}
.dots span:first-child{background:var(--white)}

/* testimonial */
.section-title{left:0;width:1200px;text-align:center;font-size:29px;font-weight:400}
.testi-title{top:646px;color:var(--accent)}
.avatar{left:259px;top:686px;width:194px;height:194px;border-radius:50%;background:radial-gradient(circle at 50% 45%,#c9a08c 0%,#8e5a45 55%,#4a4545 100%)}
.quote{left:484px;top:708px;width:500px;font-size:13.5px;line-height:25px;color:var(--muted)}
.qmark{position:absolute;font-size:40px;color:#b5b5b5;font-family:Georgia,serif;line-height:1}
.qmark.open{left:463px;top:702px}
.qmark.close{left:857px;top:786px}
.person{left:484px;top:824px}
.person b{display:block;font-size:16px;font-weight:600;color:var(--ink);line-height:22px}
.person span{font-size:12.5px;color:var(--muted)}

/* uses */
.uses{left:0;top:944px;width:1200px;height:525px;background:var(--band)}
.uses-title{top:1004px;font-size:27px;line-height:35px}
.svc{width:330px}
.svc h3{font-size:17px;font-weight:400;color:var(--ink);margin-bottom:6px}
.svc p{font-size:11.5px;line-height:18px;color:var(--muted)}
.svc.left{text-align:right}
.svc-icon{width:66px;height:66px;border-radius:50%;background:var(--white);border:2px solid #e2e2e2;display:flex;align-items:center;justify-content:center}

/* why */
.why-title{top:1529px;font-size:29px}
.hex-text{width:200px;text-align:center;color:var(--white)}
.hex-text h4{font-size:16px;font-weight:700;margin-bottom:8px;white-space:nowrap}
.hex-text p{font-size:10.5px;line-height:17px}

/* contact */
.contact{left:0;top:1888px;width:1200px;height:478px;background:linear-gradient(120deg,#eeeeee 0%,#f6f6f6 40%,#f3f3f3 70%,#e2e2e2 100%)}
.contact-title{top:1935px;font-size:32px}
.contact-sub{top:1988px;left:0;width:1200px;text-align:center;font-size:19px;line-height:28px;color:#444}
.field{background:var(--white);border:1px solid #cfcfcf;font-size:13px;color:var(--muted);padding:10px 16px}
.submit{left:534px;top:2280px;width:136px;height:38px;font-size:14px}

/* footer */
.foot-h{top:2420px;color:var(--accent);font-size:21px;font-weight:400}
.foot-links{top:2456px;font-size:14px;color:#555;line-height:28.5px;list-style:none}
.social{top:2452px;width:32px;height:32px;border-radius:50%;background:var(--accent)}
.foot-brand{left:845px;top:2452px;color:#555}
.foot-brand .mark{border-color:#555}
.rule{left:159px;top:2641px;width:884px;height:1px;background:var(--line)}
.copy{top:2656px;left:0;width:1200px;text-align:center;font-size:12px;color:#aaa}
</style>
</head>
<body>

<div class="abs hero" role="img" aria-label="Photo of a person working at a desktop monitor showing business charts, with a potted plant"></div>
<div class="abs brand" style="left:160px;top:40px"><span class="mark"></span>Quorvix</div>
<nav class="abs nav">
  <a style="left:0;top:0">Solutions</a>
  <a style="left:105px;top:0">Pricing</a>
  <a style="left:190px;top:0">Company</a>
  <a style="left:300px;top:0">Get free Quote</a>
</nav>
<h1 class="abs hero-title">Turn Websites Into Structured Data feeds</h1>
<p class="abs hero-sub">Easily get structured data feeds from any website through our cloud based data &nbsp;as a service platform. No programming ,Servers or Expensive Softwares required</p>
<div class="abs btn hero-btn">Get free Quote</div>
<div class="abs dots"><span></span><span></span><span></span><span></span></div>

<h2 class="abs section-title testi-title">Testimonials</h2>
<div class="abs avatar" role="img" aria-label="Portrait photo of the client"></div>
<span class="qmark open">“</span>
<p class="abs quote">Quorvix was very responsive and quick to deliver. They were happy to do 2 iterations on the initial data scrape set up to ensure we got the info we needed moving forward. They delivered great results were others had previously failed. We’re excited to have found this service and will be looking</p>
<span class="qmark close">”</span>
<div class="abs person"><b>Mara Lindqvist</b><span>Director of Business Development @ LaunchNest</span></div>

<section class="abs uses"></section>
<h2 class="abs section-title uses-title">Businesses of all sizes use our clean data feeds to Quickly build apps,<br>Experiment with fresh ideas and Solve business problems</h2>

<div class="abs svc left" style="left:134px;top:1136px"><h3>ECommerce</h3><p>Our Ecommerce product data feeds gives you access<br>to structured product information like pricing,.</p></div>
<div class="abs svc-icon" style="left:483px;top:1137px"><svg width="30" height="26" viewBox="0 0 30 26"><rect x="1" y="1" width="28" height="24" fill="none" stroke="#f7b016" stroke-width="2"/><line x1="1" y1="7" x2="29" y2="7" stroke="#f7b016" stroke-width="2"/><path d="M8 11h3l2 7h8l2-5H12" fill="none" stroke="#f7b016" stroke-width="2"/></svg></div>
<div class="abs svc left" style="left:134px;top:1232px"><h3>Lead Generation</h3><p>We help find quality leads for your business by<br>extracting public &nbsp;data from all kind of sources like</p></div>
<div class="abs svc-icon" style="left:483px;top:1232px"><svg width="30" height="30" viewBox="0 0 30 30"><circle cx="15" cy="9" r="6" fill="#f7b016"/><path d="M4 28c0-7 5-11 11-11s11 4 11 11z" fill="#f7b016"/></svg></div>
<div class="abs svc left" style="left:134px;top:1336px"><h3>SERP Tracking</h3><p>Our SERP data feeds gives companies access to<br>Search Engine rankings of any keywords from search</p></div>
<div class="abs svc-icon" style="left:483px;top:1335px"><svg width="34" height="24" viewBox="0 0 34 24"><path d="M1 18l8-8 6 6 10-10 8 8" fill="none" stroke="#f7b016" stroke-width="2"/><circle cx="16" cy="12" r="6" fill="none" stroke="#f7b016" stroke-width="2"/><line x1="20" y1="16" x2="25" y2="22" stroke="#f7b016" stroke-width="2"/></svg></div>

<div class="abs svc-icon" style="left:638px;top:1137px"><svg width="28" height="30" viewBox="0 0 28 30"><rect x="1" y="1" width="26" height="28" fill="none" stroke="#f7b016" stroke-width="2"/><g stroke="#f7b016" stroke-width="2"><line x1="6" y1="8" x2="22" y2="8"/><line x1="6" y1="14" x2="22" y2="14"/><line x1="6" y1="20" x2="22" y2="20"/></g></svg></div>
<div class="abs svc" style="left:726px;top:1136px"><h3>News Aggregation</h3><p>We help businesses &nbsp;build their own unique news<br>data feeds by aggregating data from news sites</p></div>
<div class="abs svc-icon" style="left:638px;top:1232px"><svg width="32" height="32" viewBox="0 0 32 32"><circle cx="16" cy="16" r="11" fill="none" stroke="#f7b016" stroke-width="2"/><circle cx="16" cy="16" r="5" fill="#f7b016"/><g stroke="#f7b016" stroke-width="2"><line x1="16" y1="0" x2="16" y2="6"/><line x1="16" y1="26" x2="16" y2="32"/><line x1="0" y1="16" x2="6" y2="16"/><line x1="26" y1="16" x2="32" y2="16"/></g></svg></div>
<div class="abs svc" style="left:726px;top:1232px"><h3>Recruiting</h3><p>We &nbsp;help recruiters &nbsp;automate scouting candidate<br>profiles from different online sources</p></div>
<div class="abs svc-icon" style="left:638px;top:1335px"><svg width="20" height="32" viewBox="0 0 20 32"><rect x="1" y="1" width="18" height="30" rx="3" fill="none" stroke="#f7b016" stroke-width="2"/><line x1="1" y1="25" x2="19" y2="25" stroke="#f7b016" stroke-width="2"/></svg></div>
<div class="abs svc" style="left:726px;top:1336px"><h3>Build your App</h3><p>We help businesses quickly build their apps on top<br>of our scalable data extraction infrastructure</p></div>

<h2 class="abs section-title why-title">Why Us</h2>
<svg class="abs" style="left:150px;top:1569px" width="900" height="260" viewBox="0 0 900 260">
  <polygon points="114,0 226,65 226,195 114,260 2,195 2,65" fill="#f7b016"/>
  <polygon points="336,0 448,65 448,195 336,260 224,195 224,65" fill="#7b7b7b"/>
  <polygon points="559,0 671,65 671,195 559,260 447,195 447,65" fill="#f7b016"/>
  <polygon points="783,0 895,65 895,195 783,260 671,195 671,65" fill="#7b7b7b"/>
  <g fill="none" stroke="#fff" stroke-width="2.5">
    <rect x="90" y="50" width="48" height="48"/><circle cx="114" cy="50" r="7"/><circle cx="138" cy="74" r="7"/>
    <ellipse cx="336" cy="54" rx="22" ry="7"/><path d="M314 54v40c0 4 10 8 22 8s22-4 22-8V54M314 67c0 4 10 8 22 8s22-4 22-8M314 80c0 4 10 8 22 8s22-4 22-8"/>
    <path d="M536 52v46h48M542 90l12-14 10 8 16-20"/>
    <path d="M758 82h20l6 6h14v10h-40M758 84v16"/><path d="M768 48h30M768 58h30M768 68h30" stroke-dasharray="4 3"/>
  </g>
</svg>
<div class="abs hex-text" style="left:164px;top:1683px"><h4>Solve Real Problems</h4><p>Quorvix provides a fully managed Big Data As A Service. You can easily plug our data feeds into your favourite</p></div>
<div class="abs hex-text" style="left:386px;top:1683px"><h4>Clean Data</h4><p>We follow a strict quality assurance process and a Machine learning based Q&amp;A system to ensure the</p></div>
<div class="abs hex-text" style="left:609px;top:1683px"><h4>Customer Success</h4><p>Ensuring Customer success is our first priority. Our customer success team consists of experienced</p></div>
<div class="abs hex-text" style="left:833px;top:1683px"><h4>Data Wrangling Support</h4><p>Quorvix helps those who need data wrangling support by providing profiling, filtering</p></div>

<section class="abs contact" role="img" aria-label="Photo of a white desk with keyboard, mouse, notebook and a cup of coffee"></section>
<h2 class="abs section-title contact-title">We’re here to help!</h2>
<p class="abs contact-sub">We’re friendly and available to help solve your data extraction problems.<br>Fill the form below to contact us. Let us do the heavy lifting for youa</p>
<div class="abs field" style="left:292px;top:2079px;width:378px;height:40px">Email address</div>
<div class="abs field" style="left:677px;top:2079px;width:233px;height:40px">Your Monthly Budget</div>
<div class="abs field" style="left:292px;top:2130px;width:618px;height:130px">Your Message</div>
<div class="abs btn submit">SUBMIT</div>

<h3 class="abs foot-h" style="left:157px">Quick Links</h3>
<ul class="abs foot-links" style="left:161px"><li>Blog</li><li>Answers</li><li>Case Studies</li><li>Slide</li></ul>
<h3 class="abs foot-h" style="left:379px">Resources</h3>
<ul class="abs foot-links" style="left:383px"><li>Startup Partner program</li><li>FAQ</li><li>Careers</li></ul>
<h3 class="abs foot-h" style="left:617px">Follow Us</h3>
<div class="abs social" style="left:618px"></div>
<div class="abs social" style="left:661px"></div>
<div class="abs social" style="left:704px"></div>
<div class="abs social" style="left:747px"></div>
<div class="abs brand foot-brand"><span class="mark"></span>Quorvix</div>
<div class="abs rule"></div>
<p class="abs copy">© 2016 Company Name &nbsp;All right reserved &nbsp;Term of Use</p>

</body>
</html>
```